" LOCAÇÃO DE EQUIPAMENTOS PARA EMPRESAS DE TERRAPLENAGEM, CONSTRUTORAS OU DIRETAMENTE PARA PRODUTORES RURAIS. dados pro cartão: Tiago Benvenuti de Souza Tel 51 44 99481-3052 Tel 55 65 99735-2140 e-mail: tiago.tbs@caixapostalnova.com.br e-mail: engenharia.vkpa@caixapostalnova.com.br Vale Serrano-PR "

```html
<!DOCTYPE html>
<html lang="pt-BR">
<head>
<meta charset="utf-8">
<title>Vantra Locação de Máquinas – Cartão de Visita</title>
<link href="https://fonts.googleapis.com/css2?family=Montserrat:wght@700;800&family=Barlow:wght@500;600&display=swap" rel="stylesheet">
<style>
  :root {
    --bg: #e4e4e4;
    --navy: #17325f;
    --orange: #ee7a2d;
    --white: #ffffff;
  }
  * { box-sizing: border-box; margin: 0; padding: 0; }
  html, body {
    width: 1200px; height: 1200px; overflow: hidden;
    background: var(--bg);
  }
  .canvas { position: relative; width: 1200px; height: 1200px; }

  .card {
    position: absolute;
    left: 206px; width: 788px; height: 436px;
    border-radius: 28px;
    overflow: hidden;
  }
  .card--front { top: 150px; background: var(--white); }
  .card--back { top: 614px; background: var(--navy); }

  .brand {
    display: flex; flex-direction: column; align-items: center;
    font-family: "Montserrat", sans-serif;
  }
  .brand__row { display: flex; align-items: center; gap: 16px; }
  .brand__mark { display: block; background: var(--orange); }
  .brand__name { font-weight: 800; letter-spacing: 0.02em; line-height: 1; }
  .brand__tagline {
    font-weight: 700; letter-spacing: 0.12em; text-transform: uppercase; line-height: 1;
  }

  .card--front .brand { position: absolute; left: 0; right: 0; top: 168px; }
  .card--front .brand__mark { width: 52px; height: 52px; }
  .card--front .brand__name { font-size: 78px; color: var(--navy); }
  .card--front .brand__tagline { font-size: 17px; color: var(--navy); margin-top: 12px; }

  .card--back .brand { position: absolute; left: 24px; width: 250px; top: 186px; }
  .card--back .brand__row { gap: 10px; }
  .card--back .brand__mark { width: 28px; height: 28px; }
  .card--back .brand__name { font-size: 42px; color: var(--white); }
  .card--back .brand__tagline { font-size: 10px; color: var(--white); margin-top: 7px; letter-spacing: 0.08em; }

  .divider {
    position: absolute; left: 290px; top: 150px; width: 2px; height: 134px;
    background: var(--white);
  }

  .contact {
    position: absolute; left: 306px; top: 150px;
    list-style: none;
    font-family: "Barlow", sans-serif; font-weight: 500;
    font-size: 19px; color: var(--white); line-height: 1;
  }
  .contact__item { display: flex; align-items: center; gap: 8px; height: 34px; }
  .contact__item--name { font-weight: 600; font-size: 20px; }
  .contact__icon { width: 16px; height: 16px; flex: none; fill: var(--white); }
</style>
</head>
<body>
<main class="canvas">

  <section class="card card--front" aria-label="Frente do cartão">
    <div class="brand">
      <div class="brand__row">
        <span class="brand__mark"></span>
        <span class="brand__name">VANTRA</span>
      </div>
      <span class="brand__tagline">Locação de Máquinas</span>
    </div>
  </section>

  <section class="card card--back" aria-label="Verso do cartão">
    <div class="brand">
      <div class="brand__row">
        <span class="brand__mark"></span>
        <span class="brand__name">VANTRA</span>
      </div>
      <span class="brand__tagline">Locação de Máquinas</span>
    </div>

    <span class="divider"></span>

    <ul class="contact">
      <li class="contact__item contact__item--name">
        <svg class="contact__icon" viewBox="0 0 16 16" aria-hidden="true"><circle cx="8" cy="4.5" r="3.5"/><path d="M1 16c0-4 3-6.5 7-6.5s7 2.5 7 6.5z"/></svg>
        Tiago Benvenuti de Souza
      </li>
      <li class="contact__item">
        <svg class="contact__icon" viewBox="0 0 16 16" aria-hidden="true"><path d="M4 1h2.5l1.2 3.5-1.8 1.3c0.9 1.8 2.3 3.2 4.1 4.1l1.3-1.8L14.8 9.5V12c0 1.2-1 2.2-2.2 2.1C6.6 13.7 2.3 9.4 1.9 3.4 1.8 2.1 2.8 1 4 1z"/></svg>
        Tel 51 44 99481-3052
      </li>
      <li class="contact__item">
        <svg class="contact__icon" viewBox="0 0 16 16" aria-hidden="true"><path d="M8 0.5a7.5 7.5 0 0 0 0 15h3v-1.6H8a5.9 5.9 0 1 1 5.9-5.9v0.8c0 0.8-0.5 1.3-1.1 1.3s-1.1-0.5-1.1-1.3V4.6h-1.5v0.6A3.3 3.3 0 1 0 10.5 10a2.7 2.7 0 0 0 2.3 1.3c1.5 0 2.7-1.1 2.7-2.9V8A7.5 7.5 0 0 0 8 0.5zm0 5.6a1.9 1.9 0 1 1 0 3.8 1.9 1.9 0 0 1 0-3.8z"/></svg>
        e-mail: engenharia.vkpa@caixapostalnova.com.br
      </li>
      <li class="contact__item">
        <svg class="contact__icon" viewBox="0 0 16 16" aria-hidden="true"><path d="M8 0.5a5.5 5.5 0 0 0-5.5 5.5c0 4 5.5 9.5 5.5 9.5s5.5-5.5 5.5-9.5A5.5 5.5 0 0 0 8 0.5zm0 3.3a2.2 2.2 0 1 1 0 4.4 2.2 2.2 0 0 1 0-4.4z"/></svg>
        Vale Serrano-PR
      </li>
    </ul>
  </section>

</main>
</body>
</html>
```